Professional Website

We are looking for a new website for our Staffing Company. Attached is a document with all the details and pages needed along with some examples of others websites.

We want a professional Look and feel around the same color theme as the attached Amber Compass.

We currently host our site on PageLoom.io. If the winning designer can also add to PageLoom, that is a plus.

```html
<!DOCTYPE html>
<html lang="en">
<head>
<meta charset="utf-8">
<title>WorkBridge — Staffing</title>
<link href="https://fonts.googleapis.com/css2?family=Poppins:wght@400;500;600;700;800&display=swap" rel="stylesheet">
<style>
:root{
  --brand-blue:#2a2d94;
  --ink:#1f1f1f;
  --footer-dark:#262626;
  --band-grey:#e6e6e6;
  --white:#ffffff;
  --muted-line:#4a4a4a;
  --to-top:#555555;
}
*{margin:0;padding:0;box-sizing:border-box}
html,body{width:758px;height:1200px;overflow:hidden;background:var(--white)}
body{position:relative;font-family:'Poppins',sans-serif;color:var(--ink)}
.layer{position:absolute;left:0;top:0}
.site-header{position:absolute;left:0;top:0;width:758px;height:72px;z-index:3}
.brand-name{position:absolute;left:56px;top:20px;font-weight:700;font-size:25px;letter-spacing:-0.5px;color:var(--white);line-height:1}
.main-nav{position:absolute;top:31px;left:318px;display:flex;gap:14px}
.main-nav a{color:var(--white);text-decoration:none;font-size:8.2px;font-weight:600;white-space:nowrap}
.hotline{position:absolute;display:flex;align-items:center;gap:9px}
.hotline .label{font-size:7.5px;font-weight:600;color:var(--white);line-height:1.2}
.hotline .number{font-size:11.5px;font-weight:700;color:var(--white);line-height:1.2}
.header-hotline{left:580px;top:18px}
.hero-title{position:absolute;top:163px;left:0;width:758px;text-align:center;color:var(--white);font-weight:700;font-size:44px;line-height:56px;letter-spacing:-0.5px;z-index:2}
.scroll-cue{position:absolute;top:391px;left:349px;width:60px;text-align:center;color:var(--white);font-size:7.5px;font-weight:600;z-index:2}
.scroll-cue svg{display:block;margin:3px auto 0}
.about{position:absolute;left:56px;top:590px;width:310px}
.about .kicker{margin-left:9px;font-size:17px;font-weight:600;line-height:1.3}
.about h2{font-size:41px;font-weight:800;line-height:1.05;letter-spacing:-0.5px}
.about .rule{width:36px;height:2px;background:var(--band-grey);margin:10px 0 12px}
.about p{font-size:9.6px;line-height:14px;margin-bottom:10px;color:var(--ink)}
.footer-brand{position:absolute;left:132px;top:1062px;font-weight:700;font-size:29px;letter-spacing:-0.5px;color:var(--white);line-height:1}
.footer-col{position:absolute;top:1043px}
.footer-col h3{font-size:12.5px;font-weight:700;color:var(--white);margin-bottom:8px}
.footer-col li{list-style:none;font-size:9.5px;color:#d8d8d8;line-height:17px}
.areas{left:352px}
.contact{left:504px}
.footer-hotline{left:504px;top:1075px}
.footer-rule{position:absolute;left:56px;top:1159px;width:646px;height:1px;background:var(--muted-line)}
.copyright{position:absolute;top:1172px;left:0;width:758px;text-align:center;color:var(--white);font-size:8.5px;font-weight:500}
.to-top{position:absolute;left:708px;top:1142px}
</style>
</head>
<body>

<svg class="layer" width="758" height="1200" viewBox="0 0 758 1200" aria-hidden="false">
  <defs>
    <linearGradient id="heroTone" x1="0" y1="0" x2="1" y2="1">
      <stop offset="0" stop-color="#3b3734"/>
      <stop offset="0.45" stop-color="#6a4a3a"/>
      <stop offset="0.75" stop-color="#5a4a45"/>
      <stop offset="1" stop-color="#3c3a3d"/>
    </linearGradient>
    <linearGradient id="teamTone" x1="0" y1="0" x2="1" y2="1">
      <stop offset="0" stop-color="#cdb7a5"/>
      <stop offset="0.5" stop-color="#b87a52"/>
      <stop offset="1" stop-color="#2f3b43"/>
    </linearGradient>
    <linearGradient id="dataTone" x1="0" y1="0" x2="1" y2="1">
      <stop offset="0" stop-color="#3aa6c0"/>
      <stop offset="0.55" stop-color="#6b8aa0"/>
      <stop offset="1" stop-color="#1d2c3a"/>
    </linearGradient>
  </defs>

  <polygon points="0,0 758,0 758,354 0,531" fill="url(#heroTone)" role="img" aria-label="Photo: hands passing a document across a desk"/>
  <rect x="0" y="0" width="758" height="531" fill="#000" opacity="0.18"/>
  <polygon points="0,531 758,354 758,396" fill="var(--brand-blue)"/>

  <polygon points="614,470 830,686 614,902 398,686" fill="url(#teamTone)" role="img" aria-label="Photo: team raising hands together for a high five"/>
  <polygon points="493,698 588,793 493,888 398,793" fill="url(#dataTone)" stroke="var(--white)" stroke-width="2.5" role="img" aria-label="Photo: tablet showing business figures"/>
  <circle cx="599" cy="780" r="18" fill="none" stroke="var(--white)" stroke-width="1.2"/>

  <polygon points="0,879 758,1016 758,1200 0,1200" fill="var(--footer-dark)"/>
  <polygon points="0,879 758,1016 758,1058" fill="var(--band-grey)"/>
</svg>

<header class="site-header">
  <div class="brand-name">WorkBridge</div>
  <nav class="main-nav">
    <a href="#">EMPLOYEE LOGIN</a>
    <a href="#">SWIFT CARD LOGIN</a>
    <a href="#">HARBOR BANK LOGIN</a>
  </nav>
  <div class="hotline header-hotline">
    <svg width="36" height="36" viewBox="0 0 36 36"><polygon points="18,0 36,18 18,36 0,18" fill="var(--brand-blue)"/><path d="M13 12c1-1 2-1 2.5 0l1.5 2.5c.4.7 0 1.3-.6 1.7l-.8.5c.6 1.6 1.9 2.9 3.5 3.5l.5-.8c.4-.6 1-1 1.7-.6l2.5 1.5c1 .5 1 1.5 0 2.5-1.5 1.5-3.5 1.3-6-.6-2-1.5-3.3-2.8-4.6-4.8-1.6-2.4-1.7-4.1-.2-5.4z" fill="var(--white)"/></svg>
    <div><div class="label">HOTLINE</div><div class="number">555-014-2200</div></div>
  </div>
</header>

<h1 class="hero-title">I’m looking for a Job<br>I need Employees</h1>

<div class="scroll-cue">SCROLL
  <svg width="12" height="18" viewBox="0 0 12 18"><rect x="1" y="1" width="10" height="16" rx="5" fill="none" stroke="var(--white)" stroke-width="1.2"/><line x1="6" y1="4" x2="6" y2="7.5" stroke="var(--white)" stroke-width="1.2"/></svg>
</div>

<section class="about">
  <div class="kicker">How we are</div>
  <h2>Awesome!</h2>
  <div class="rule"></div>
  <p>Greatest part of our daily job is that we are constantly bringing people together.</p>
  <p>Our Clients come to us in search of the perfect candidate and the job hunters approach us when they are in need of a job or looking for their next exciting role.</p>
  <p>Being able to work with and connect the two is incredibly satisfying. Not to mention that in today's current job market, employers are fighting for the top talent. This makes our employees and partners grateful for the help in finding it!</p>
</section>

<footer>
  <div class="footer-brand">WorkBridge</div>
  <div class="footer-col areas">
    <h3>Areas we service</h3>
    <ul><li>Cedar Point</li><li>Millbrook</li><li>Westhaven</li></ul>
  </div>
  <div class="footer-col contact"><h3>Contact Us</h3></div>
  <div class="hotline footer-hotline">
    <svg width="36" height="36" viewBox="0 0 36 36"><polygon points="18,0 36,18 18,36 0,18" fill="var(--brand-blue)"/><path d="M13 12c1-1 2-1 2.5 0l1.5 2.5c.4.7 0 1.3-.6 1.7l-.8.5c.6 1.6 1.9 2.9 3.5 3.5l.5-.8c.4-.6 1-1 1.7-.6l2.5 1.5c1 .5 1 1.5 0 2.5-1.5 1.5-3.5 1.3-6-.6-2-1.5-3.3-2.8-4.6-4.8-1.6-2.4-1.7-4.1-.2-5.4z" fill="var(--white)"/></svg>
    <div><div class="label">HOTLINE</div><div class="number">555-014-2200</div></div>
  </div>
  <div class="footer-rule"></div>
  <div class="copyright">© Copyright 2022 WorkBridge All Rights Reserved</div>
  <svg class="to-top" width="36" height="36" viewBox="0 0 36 36"><polygon points="18,0 36,18 18,36 0,18" fill="var(--to-top)"/><polyline points="15.5,19.5 18,17 20.5,19.5" fill="none" stroke="var(--white)" stroke-width="1.3"/></svg>
</footer>

</body>
</html>
```